Carpet cleaning company focused on high quality needs business cards

We are a growing company that just merged with another company and need to design a new business card. We do both residential as well as commercial cleaning. We do carpet, tile & grout, upholstery, hard floors, and stain & pet odor removal. We treat our customers like family and strive to achieve outstanding results with every job.

```html
<!DOCTYPE html>
<html lang="en">
<head>
<meta charset="utf-8">
<title>Kinfolk Steam Crew Cleaning – Business Cards</title>
<link href="https://fonts.googleapis.com/css2?family=Open+Sans:wght@600;700;800&family=Poppins:wght@400&family=Fira+Sans+Extra+Condensed:wght@600&display=swap" rel="stylesheet">
<style>
  :root {
    --backdrop: #828282;
    --card: #ffffff;
    --brand-red: #ef4642;
    --ink: #1e1e1e;
    --ink-soft: #2d2d2d;
    --link-navy: #1f3558;
    --art-blue: #3b86c4;
    --art-tan: #e9dcc4;
  }
  * { box-sizing: border-box; margin: 0; padding: 0; }
  html, body {
    width: 1093px; height: 1200px; overflow: hidden;
    background: var(--backdrop);
  }
  .sheet { position: relative; width: 1093px; height: 1200px; }

  .card {
    position: absolute; left: 264px; width: 580px; height: 357px;
    background: var(--card); overflow: hidden;
  }
  .card--front { top: 226px; }
  .card--back { top: 620px; }

  /* Front */
  .person { position: absolute; left: 26px; top: 47px; }
  .person__name {
    font: 700 21px/1 "Open Sans", sans-serif; color: var(--brand-red);
    letter-spacing: -0.2px;
  }
  .person__title {
    font: 400 16.5px/1 "Poppins", sans-serif; color: var(--ink-soft);
    margin-top: 5px;
  }
  .address {
    position: absolute; left: 27px; top: 174px;
    font: 400 16.5px/21px "Poppins", sans-serif; color: var(--ink-soft);
  }
  .contacts { position: absolute; left: 25px; top: 259px; list-style: none; }
  .contacts li {
    display: flex; align-items: center; height: 24px;
    font: 400 16.5px/1 "Poppins", sans-serif; color: var(--ink-soft);
  }
  .contacts svg { width: 22px; height: 22px; margin-right: 6px; flex: none; }
  .contacts .accent { color: var(--link-navy); }
  .front-art {
    position: absolute; left: 270px; top: 28px; width: 310px; height: 329px;
    background: linear-gradient(160deg, #ffffff 0%, var(--art-tan) 35%, var(--art-blue) 65%, var(--brand-red) 100%);
    clip-path: polygon(48% 0, 70% 0, 100% 40%, 100% 100%, 0 100%, 10% 60%);
    opacity: 0.9;
  }

  /* Back */
  .brand {
    position: absolute; left: 115px; top: 140px;
    display: flex; align-items: flex-end; gap: 14px;
  }
  .brand__square { width: 150px; height: 93px; background: var(--brand-red); }
  .brand__name {
    font: 800 27px/1.05 "Open Sans", sans-serif; color: var(--ink);
    letter-spacing: -0.3px;
  }
  .service-band {
    position: absolute; left: 0; top: 259px; width: 100%; height: 38px;
    background: var(--brand-red); color: #fff;
    font: 700 20px/38px "Open Sans", sans-serif; text-align: center;
    letter-spacing: -0.2px;
  }
  .service-list {
    position: absolute; left: 0; top: 307px; width: 100%;
    text-align: center; font: 600 19.5px/26px "Fira Sans Extra Condensed", sans-serif;
    color: var(--ink);
  }
  .service-list .dot { color: var(--brand-red); margin: 0 3px; }
</style>
</head>
<body>
<main class="sheet">

  <section class="card card--front">
    <div class="person">
      <p class="person__name">DANIEL CARTER</p>
      <p class="person__title">Managing Director</p>
    </div>
    <p class="address">421, Address line here<br>Country Name, 45452</p>
    <ul class="contacts">
      <li>
        <svg viewBox="0 0 22 22" aria-hidden="true"><circle cx="11" cy="11" r="10" fill="none" stroke="#ef4642" stroke-width="1.6"/><path d="M7.5 6.5l2 0 1 2.5-1.3 1a6 6 0 0 0 3 3l1-1.3 2.5 1v2a1 1 0 0 1-1 1A8 8 0 0 1 6.5 7.5a1 1 0 0 1 1-1z" fill="#ef4642"/></svg>
        044-123 456 789
      </li>
      <li>
        <svg viewBox="0 0 22 22" aria-hidden="true"><circle cx="11" cy="11" r="10" fill="none" stroke="#ef4642" stroke-width="1.6"/><rect x="6" y="7.5" width="10" height="7" fill="#ef4642"/><path d="M6 7.5l5 4 5-4" fill="none" stroke="#fff" stroke-width="1"/></svg>
        info@webname.com
      </li>
      <li>
        <svg viewBox="0 0 22 22" aria-hidden="true"><circle cx="11" cy="11" r="10" fill="none" stroke="#ef4642" stroke-width="1.6"/><circle cx="11" cy="11" r="5.5" fill="#ef4642"/><path d="M5.5 11h11M11 5.5v11M7 8.5h8M7 13.5h8" stroke="#fff" stroke-width="0.8"/></svg>
        www.<span class="accent">websitename</span>.com
      </li>
    </ul>
    <div class="front-art" role="img" aria-label="Illustration of a cheerful cleaning technician holding a steam cleaning wand over a red burst"></div>
  </section>

  <section class="card card--back">
    <div class="brand">
      <span class="brand__square" aria-hidden="true"></span>
      <p class="brand__name">Kinfolk<br>Steam Crew<br>Cleaning</p>
    </div>
    <p class="service-band">RESIDENTIAL &amp; COMMERCIAL CLEANING</p>
    <p class="service-list">Carpet<span class="dot">•</span>Tile &amp; Grout<span class="dot">•</span>Upholstery<span class="dot">•</span>Hard floors &amp; Stain<span class="dot">•</span>Pet Odor Removal</p>
  </section>

</main>
</body>
</html>
```